Powerpoint Design for AI Consulting Company

Description
Velmora Quill Industries is a consulting and technology company that engineers AI transformations, automation, and decision intelligence for financial firms, mining companies, and supply chains.
We already have a logo and brand colors (see attached). We need a professional, modern PowerPoint template that reflects our brand identity and positioning.
Key Requirements
Use our logo and color palette (deep blue, orange, white/black backgrounds).
Clean, modern design with subtle technology-inspired elements (data flows, AI networks, abstract systems).
Must feel sophisticated, bold, and boardroom-ready for executive presentations.
Templates should support both dark and light backgrounds.
Deliverables
A reusable PowerPoint template (.PPTX) with at least these layouts:
Title / Cover slide – dramatic, logo placement, tagline space.
Agenda slide – clean, structured layout.
Section divider slides – strong use of brand colors.
Content slides – text + image, text + icon.
Charts & data slides – bar, line, pie, comparison table, infographics.
Case study / example project slide. - ROI / Transformation Journey
Timeline / roadmap slide.
Team profile slide.
Reframe Slide – A provocative insight that reframes the client’s current thinking.
Options & Trade-offs Slide – Matrix showing different paths and consequences.
Execution Roadmap Slide – Step-by-step phased implementation view.
Closing / thank-you slide with contact details.
Style Guide
Colors: Primary – deep blue (#0D3559), Secondary – orange (#E87722), Accents – silver/white.
Fonts: Modern sans-serif (e.g., Montserrat, Lato, or similar).
Visual elements: Abstract technology, data-inspired graphics, mathematical motifs. Avoid clutter or overly “sci-fi” looks.
Tone: Premium consulting + innovative AI firm.
Target Market(s)
Velmora Quill Industries’ target market is senior decision-makers in finance, mining, and supply chains, where complexity, risk, and ROI pressure are high. Primary buyers include family offices, boutique wealth managers, super funds, and mining/supply chain executives, who value insight-driven strategies, automation, and decision intelligence. A secondary market includes professional services (accounting, legal, medical) and regulated SMEs (daycare, aged care, community services) burdened by admin and compliance. The slide deck must appeal to a boardroom audience — authoritative, data-driven, and visually clean — while remaining flexible enough to adapt for SME professional services.
Look and feel
Each slider illustrates characteristics of the customer's brand and the style your logo design should communicate.

```html
<!DOCTYPE html>
<html lang="en">
<head>
<meta charset="utf-8">
<title>Velmora Quill Industries – Presentation Template</title>
<link href="https://fonts.googleapis.com/css2?family=Poppins:wght@400;500;600;700;800&display=swap" rel="stylesheet">
<style>
:root{
  --blue:#0D4E94;
  --blue-deep:#0D3559;
  --orange:#D9530A;
  --orange-soft:#E87722;
  --ink:#1c1c1c;
  --grey:#5a5a5a;
  --bar:#2a2a2a;
  --canvas:#ffffff;
  --paper:#ffffff;
}
*{margin:0;padding:0;box-sizing:border-box}
html,body{width:1200px;height:835px;overflow:hidden;background:var(--canvas)}
body{position:relative;font-family:'Poppins',sans-serif;color:var(--ink)}
.slide{position:absolute;width:351px;height:197px;background:var(--paper);overflow:hidden;box-shadow:0 4px 14px rgba(0,0,0,.16)}
.col1{left:33px}.col2{left:426px}.col3{left:818px}
.row1{top:52px}.row2{top:315px}.row3{top:577px}
.abs{position:absolute}

/* shared slide furniture */
.brand-mini{position:absolute;right:5px;top:4px;font-size:4.6px;font-weight:700;color:var(--blue);line-height:1.05;text-align:right;text-transform:uppercase;display:flex;align-items:center;gap:2px}
.brand-mini .dot{width:5px;height:5px;border-radius:50%;background:var(--orange)}
.footer-web{position:absolute;left:0;bottom:4px;width:76px;height:11px;background:var(--bar);color:#fff;font-size:3.8px;display:flex;align-items:center;gap:3px;padding-left:5px}
.footer-web .globe{width:6px;height:6px;border-radius:50%;background:#fff;border:1px solid var(--blue)}
.footer-copy{position:absolute;left:0;right:0;bottom:7px;text-align:center;font-size:3.6px;color:var(--grey)}
.footer-page{position:absolute;right:0;bottom:4px;width:24px;height:11px;background:var(--blue);color:#fff;font-size:3.8px;display:flex;align-items:center;justify-content:center}
.heading{position:absolute;font-weight:600;font-size:10px;color:var(--ink);display:flex;align-items:center;gap:5px;white-space:nowrap}
.heading::before{content:"";width:1.2px;height:10px;background:var(--orange)}
.body-copy{font-size:4.3px;line-height:1.75;color:var(--grey);text-align:justify}

/* cover */
.cover{background:linear-gradient(120deg,#f4f6f8 0%,#eef2f4 55%,#e6eef2 100%)}
.cover .name{position:absolute;left:14px;top:31px;font-size:12px;font-weight:700;color:var(--blue);line-height:1.05;display:flex;align-items:center;gap:4px}
.cover .name .dot{width:9px;height:9px;border-radius:50%;background:var(--orange)}
.cover .tagline{position:absolute;left:11px;top:75px;font-size:11px;font-weight:800;color:var(--blue);line-height:1.45;letter-spacing:-.2px}
.cover .tagline em{font-style:normal;color:var(--orange)}
.cover .network{position:absolute;right:0;top:0;width:200px;height:197px;background:radial-gradient(circle at 60% 40%,rgba(13,78,148,.10),rgba(255,255,255,0) 70%)}
.contact-list{position:absolute;left:0;top:144px;list-style:none}
.contact-list li{display:flex;align-items:center;height:12.5px;font-size:5px;color:var(--ink)}
.contact-list .dash{width:7px;height:1px;background:var(--blue);margin-right:6px}
.contact-list .ic{width:7px;height:7px;border-radius:50%;background:var(--blue);margin-right:6px}

/* agenda */
.agenda-title{left:50%;transform:translateX(-50%);top:24px}
.agenda-item{position:absolute;width:126px;height:17px;color:#fff;font-size:4.3px;display:flex;align-items:center;justify-content:space-between;padding:0 8px 0 9px;box-shadow:0 1px 2px rgba(0,0,0,.2)}
.agenda-item b{font-size:5px;font-weight:600}
.agenda-item.blue{background:var(--blue)}
.agenda-item.orange{background:var(--orange)}

/* about */
.about-photo{position:absolute;left:0;top:0;width:351px;height:197px;background:linear-gradient(90deg,#140c08 0%,#3a1a08 22%,#c2560f 38%,#f08a2a 45%,#f6e2cf 58%,#ffffff 70%)}
.about-title{left:176px;top:59px}
.about-copy{position:absolute;left:176px;top:78px;width:125px}

/* vision */
.hex-art{position:absolute;left:24px;top:13px;width:150px;height:170px}
.vision-title{left:197px;top:43px}
.vision-copy{position:absolute;left:197px;top:60px;width:126px}
.vision-copy p+p{margin-top:3px}

/* what we do */
.wwd-title{left:50%;transform:translateX(-50%);top:17px}
.wwd-intro{position:absolute;left:46px;right:46px;top:36px;text-align:center;font-size:4.4px;line-height:1.75;color:var(--grey)}
.service{position:absolute;width:78px;border-left:.6px solid #bbb;padding-left:5px}
.service .num{position:absolute;left:5px;top:-1px;font-size:11px;font-weight:600;color:var(--orange);line-height:1}
.service h4{margin-left:12px;font-size:3.9px;font-weight:600;line-height:1.3;text-transform:uppercase;min-height:11px}
.service p{margin-top:3px;font-size:3.2px;line-height:1.75;color:var(--grey);text-align:justify}

/* case studies */
.cs-title{left:9px;top:6px}
.world{position:absolute;left:14px;top:28px;width:320px;height:140px;border-radius:40% 45% 35% 40%;background:radial-gradient(ellipse at center,#eceff2 0%,#f5f6f7 60%,#fff 100%)}
.cs-node{position:absolute;width:58px;height:58px;border-radius:50%;color:#fff;text-align:center;padding:11px 6px 0;border:2.5px solid #fff;box-shadow:0 1px 4px rgba(0,0,0,.3)}
.cs-node.blue{background:var(--blue)}
.cs-node.orange{background:var(--orange)}
.cs-node h5{font-size:3.8px;font-weight:600;line-height:1.2}
.cs-node p{font-size:2.6px;line-height:1.6;margin-top:2px}
.cs-brand{position:absolute;left:134px;top:140px;width:88px;text-align:center;font-size:6.6px;font-weight:700;color:var(--blue);line-height:1.05;text-transform:uppercase}
.cs-brand small{display:block;font-size:3px;margin-top:1px}

/* team */
.team-title{left:9px;top:6px}
.team-hub{position:absolute;left:141px;top:66px;width:69px;height:69px;border-radius:50%;border:3.5px solid var(--bar);display:flex;align-items:center;justify-content:center;text-align:center;font-size:5px;font-weight:700;color:var(--blue);line-height:1.1;text-transform:uppercase;box-shadow:0 0 0 1px var(--orange)}
.member{position:absolute;width:70px}
.member .portrait{width:23px;height:24px;background:linear-gradient(160deg,#c9d3dc,#7f8f9c)}
.member h6{font-size:4px;font-weight:600;margin-top:2px}
.member .role{font-size:2.6px;color:var(--grey)}
.member p{font-size:3.1px;line-height:1.7;color:var(--grey);margin-top:2px}
.member.right{text-align:left}
.member.left{text-align:right}
.member.left .portrait{margin-left:auto}

/* contact */
.contact-band{position:absolute;left:0;top:0;width:351px;height:41px;background:var(--blue)}
.contact-band h2{position:absolute;left:27px;top:9px;font-size:13px;font-weight:800;color:#fff;letter-spacing:-.2px}
.contact-band span{position:absolute;left:28px;top:30px;width:62px;height:1.5px;background:#fff}
.contact-name{position:absolute;left:44px;top:70px;font-size:8px;font-weight:700;color:var(--blue);line-height:1.05;display:flex;align-items:center;gap:3px}
.contact-name .dot{width:7px;height:7px;border-radius:50%;background:var(--orange)}
.contact-row{position:absolute;left:42px;display:flex;gap:5px;align-items:flex-start}
.contact-row .ic{width:9px;height:9px;border-radius:50%;background:var(--blue);flex:none;margin-top:1px}
.contact-row small{display:block;font-size:3.2px;color:var(--grey)}
.contact-row span{display:block;font-size:4.2px;line-height:1.5;color:var(--ink)}
.map{position:absolute;left:172px;top:53px;width:153px;height:120px;background:linear-gradient(135deg,#efe6d2,#e4e7d8 55%,#dfe3e6)}

/* closing brand */
.brand-panel{position:absolute;left:878px;top:638px;width:232px;text-align:center}
.brand-panel .name{font-size:21px;font-weight:700;color:var(--blue);line-height:1.1;text-transform:uppercase;display:flex;align-items:center;justify-content:center;gap:8px}
.brand-panel .name .dot{width:16px;height:16px;border-radius:50%;background:var(--orange);flex:none}
.brand-panel .sub{font-size:8.6px;font-weight:600;color:var(--blue);letter-spacing:1px;margin-top:5px}
</style>
</head>
<body>

<!-- Cover -->
<section class="slide col1 row1 cover">
  <div class="network" role="img" aria-label="Faint abstract data network backdrop"></div>
  <div class="name"><span class="dot"></span><span>Velmora Quill<br>Industries</span></div>
  <h1 class="tagline">Engineering <em>AI Transformation.</em><br>Powering Intelligent Futures.</h1>
  <ul class="contact-list">
    <li><span class="dash"></span><span class="ic"></span>www.velmoraquill.com</li>
    <li><span class="dash"></span><span class="ic"></span>info@velmoraquill.com</li>
    <li><span class="dash"></span><span class="ic"></span>+1 480 555 0142</li>
  </ul>
</section>

<!-- Agenda -->
<section class="slide col2 row1">
  <div class="brand-mini"><span class="dot"></span>Velmora Quill<br>Industries</div>
  <h2 class="heading agenda-title">Agenda</h2>
  <div class="agenda-item blue" style="left:42px;top:46px">01. Agenda<b>01</b></div>
  <div class="agenda-item orange" style="left:182px;top:46px">02. Who We Are<b>02</b></div>
  <div class="agenda-item orange" style="left:42px;top:69px">02. Our Expertise<b>03</b></div>
  <div class="agenda-item blue" style="left:182px;top:69px">04. Industry Impact<b>04</b></div>
  <div class="agenda-item blue" style="left:42px;top:92px">03. Case Studies &amp; ROI<b>05</b></div>
  <div class="agenda-item orange" style="left:182px;top:92px">06. Transformation Journey<b>06</b></div>
  <div class="agenda-item orange" style="left:42px;top:115px">04. Options &amp; Trade-offs<b>07</b></div>
  <div class="agenda-item blue" style="left:182px;top:115px">08. Execution Roadmap<b>08</b></div>
  <div class="agenda-item blue" style="left:42px;top:138px">05. Our Team<b>09</b></div>
  <div class="agenda-item orange" style="left:182px;top:138px">10. Closing &amp; Next Steps<b>10</b></div>
  <div class="footer-web"><span class="globe"></span>www.velmoraquill.com</div>
  <div class="footer-copy">© 2025. ALL Rights Reserved.</div>
  <div class="footer-page">Page 02</div>
</section>

<!-- About -->
<section class="slide col3 row1">
  <div class="about-photo" role="img" aria-label="Photo of an executive silhouetted against a glowing orange data corridor"></div>
  <div class="brand-mini"><span class="dot"></span>Velmora Quill<br>Industries</div>
  <h2 class="heading about-title">About Us</h2>
  <p class="body-copy about-copy">We help finance, mining and supply chain leaders turn complexity into clear decisions. Our teams design AI systems, automation and decision intelligence that fit the way your business already works, with measurable returns at every stage. From first workshop to full rollout, we stay accountable for outcomes, risk and adoption across the whole organisation.</p>
  <div class="footer-web"><span class="globe"></span>www.velmoraquill.com</div>
  <div class="footer-copy">© 2025. ALL Rights Reserved.</div>
  <div class="footer-page">Page 02</div>
</section>

<!-- Vision & Mission -->
<section class="slide col1 row2">
  <div class="brand-mini"><span class="dot"></span>Velmora Quill<br>Industries</div>
  <svg class="hex-art" viewBox="0 0 150 170" role="img" aria-label="Hexagon collage of technology imagery: neural network, data tunnel, colourful cloud, turbine and circuit lights">
    <defs>
      <linearGradient id="gBlue" x1="0" y1="0" x2="1" y2="1"><stop offset="0" stop-color="#0b3a66"/><stop offset="1" stop-color="#2a8fd0"/></linearGradient>
      <linearGradient id="gNight" x1="0" y1="0" x2="1" y2="1"><stop offset="0" stop-color="#12081f"/><stop offset="1" stop-color="#6a1f6d"/></linearGradient>
      <linearGradient id="gCloud" x1="0" y1="0" x2="1" y2="1"><stop offset="0" stop-color="#4a6fd0"/><stop offset=".5" stop-color="#e0405a"/><stop offset="1" stop-color="#2a1a55"/></linearGradient>
      <linearGradient id="gAmber" x1="0" y1="0" x2="1" y2="1"><stop offset="0" stop-color="#3a2208"/><stop offset="1" stop-color="#e69a2a"/></linearGradient>
      <linearGradient id="gTurb" x1="0" y1="0" x2="1" y2="1"><stop offset="0" stop-color="#0d2540"/><stop offset="1" stop-color="#c25a20"/></linearGradient>
    </defs>
    <polygon points="33,0 48,8.5 48,26 33,34.5 18,26 18,8.5" fill="url(#gBlue)"/>
    <polygon points="44,30 57,37.5 57,52.5 44,60 31,52.5 31,37.5" fill="#c9551c"/>
    <polygon points="89,2 113,16 113,44 89,58 65,44 65,16" fill="url(#gNight)"/>
    <polygon points="62,66 89,82 89,114 62,130 35,114 35,82" fill="url(#gCloud)"/>
    <polygon points="115,62 132,72 132,92 115,102 98,92 98,72" fill="url(#gTurb)"/>
    <polygon points="101,104 110,109 110,119 101,124 92,119 92,109" fill="#d9530a"/>
    <polygon points="104,126 116,133 116,147 104,154 92,147 92,133" fill="url(#gAmber)"/>
  </svg>
  <h2 class="heading vision-title">Our Vision &amp; Mission</h2>
  <div class="body-copy vision-copy">
    <p>Our vision is a world where every critical decision is informed by trusted data and intelligent systems. We build AI that leaders understand, audit and rely on, so that complexity becomes a source of advantage rather than risk.</p>
    <p>Our mission is to engineer practical transformation: automation that removes friction, models that sharpen judgement and roadmaps that deliver measurable value for boards and teams.</p>
  </div>
  <div class="footer-web"><span class="globe"></span>www.velmoraquill.com</div>
  <div class="footer-copy">© 2025. ALL Rights Reserved.</div>
  <div class="footer-page">Page 04</div>
</section>

<!-- What We Do -->
<section class="slide col2 row2">
  <div class="brand-mini"><span class="dot"></span>Velmora Quill<br>Industries</div>
  <h2 class="heading wwd-title">What We Do</h2>
  <p class="wwd-intro">We combine consulting depth with engineering skill to design, build and run AI solutions for complex operations. Each engagement links strategy to delivery, so every model, workflow and dashboard serves a clear business outcome and pays back.</p>
  <div class="service" style="left:28px;top:74px"><span class="num">1.</span><h4>Full Truckload (FTL)<br>Shipping</h4><p>Route and load planning models that cut empty miles and lift fleet use.</p></div>
  <div class="service" style="left:136px;top:74px"><span class="num">2.</span><h4>Less Than Truckload (LTL)<br>Shipping</h4><p>Smart consolidation that groups orders and lowers cost per pallet moved.</p></div>
  <div class="service" style="left:243px;top:74px"><span class="num">3.</span><h4>Express and Same-Day<br>Delivery</h4><p>Real-time dispatch engines that keep urgent orders on time and visible.</p></div>
  <div class="service" style="left:28px;top:124px"><span class="num">4.</span><h4>Cross-Border<br>Transportation</h4><p>Automated customs checks that shorten border delays and reduce errors.</p></div>
  <div class="service" style="left:136px;top:124px"><span class="num">5.</span><h4>Temperature-Controlled<br>Freight</h4><p>Sensor analytics that flag cold chain risks before any product is lost.</p></div>
  <div class="service" style="left:243px;top:124px"><span class="num">6.</span><h4>Hazardous Material<br>Transport</h4><p>Compliance tracking that keeps every dangerous load safe and audited.</p></div>
  <div class="footer-web"><span class="globe"></span>www.velmoraquill.com</div>
  <div class="footer-copy">© 2025. ALL Rights Reserved.</div>
  <div class="footer-page">Page 05</div>
</section>

<!-- Case Studies & ROI -->
<section class="slide col3 row2">
  <div class="world" role="img" aria-label="Faint grey world map backdrop"></div>
  <div class="brand-mini"><span class="dot"></span>Velmora Quill<br>Industries</div>
  <h2 class="heading cs-title">Case Studies &amp; ROI</h2>
  <svg class="abs" style="left:0;top:0" width="351" height="197" viewBox="0 0 351 197">
    <g fill="none" stroke="#1c1c1c" stroke-width="1">
      <path d="M160 53 Q180 50 198 53"/>
      <path d="M102 73 L88 88"/>
      <path d="M257 73 L270 88"/>
      <path d="M64 146 L63 158"/>
      <path d="M293 146 L294 158"/>
    </g>
    <g fill="#1c1c1c"><circle cx="160" cy="53" r="1.6"/><circle cx="198" cy="53" r="1.6"/><circle cx="88" cy="88" r="1.6"/><circle cx="270" cy="88" r="1.6"/><circle cx="63" cy="158" r="1.6"/><circle cx="294" cy="158" r="1.6"/></g>
    <path d="M104 167 A74 74 0 0 1 126 114 L134 122 A63 63 0 0 0 115 167 Z" fill="#0D4E94"/>
    <path d="M126 114 A74 74 0 0 1 178 93 L178 104 A63 63 0 0 0 134 122 Z" fill="#D9530A"/>
    <path d="M178 93 A74 74 0 0 1 230 114 L222 122 A63 63 0 0 0 178 104 Z" fill="#0D4E94"/>
    <path d="M230 114 A74 74 0 0 1 252 167 L241 167 A63 63 0 0 0 222 122 Z" fill="#D9530A"/>
  </svg>
  <div class="cs-node orange" style="left:102px;top:28px"><h5>Consectetur<br>Adipiscing Elit</h5><p>Credit risk model cut review time by half for a wealth firm.</p></div>
  <div class="cs-node blue" style="left:200px;top:28px"><h5>Consectetur<br>Adipiscing Elit</h5><p>Mine haulage planning lifted ore moved per shift by 14%.</p></div>
  <div class="cs-node blue" style="left:43px;top:89px"><h5>Consectetur<br>Adipiscing Elit</h5><p>Invoice automation saved a super fund 9,000 hours a year.</p></div>
  <div class="cs-node orange" style="left:258px;top:89px"><h5>Consectetur<br>Adipiscing Elit</h5><p>Demand forecasting reduced stock holding costs by 22 percent.</p></div>
  <div class="cs-brand">Velmora Quill<br>Industries<small>Engineering AI Transformations</small></div>
  <div class="footer-web"><span class="globe"></span>www.velmoraquill.com</div>
  <div class="footer-copy">© 2024. ALL Rights Reserved.</div>
  <div class="footer-page">Page 08</div>
</section>

<!-- Our Team -->
<section class="slide col1 row3">
  <div class="brand-mini"><span class="dot"></span>Velmora Quill<br>Industries</div>
  <h2 class="heading team-title">Our Team</h2>
  <svg class="abs" style="left:0;top:0" width="351" height="197" viewBox="0 0 351 197">
    <g fill="none" stroke="#444" stroke-width=".6">
      <path d="M122 72 L131 72 L141 82"/>
      <path d="M228 72 L219 72 L210 82"/>
      <path d="M122 124 L131 124 L141 114"/>
      <path d="M228 124 L219 124 L210 114"/>
    </g>
  </svg>
  <div class="team-hub">Velmora<br>Quill<br>Industries</div>
  <div class="member left" style="left:42px;top:38px"><div class="portrait" role="img" aria-label="Portrait photo of team member"></div><h6>ELENA VARGA</h6><div class="role">CEO, Strategy</div><p>Leads board advisory and AI strategy for finance clients.</p></div>
  <div class="member right" style="left:238px;top:38px"><div class="portrait" role="img" aria-label="Portrait photo of team member"></div><h6>TOMAS REYN</h6><div class="role">CTO, Platforms</div><p>Builds data platforms and model pipelines for every rollout.</p></div>
  <div class="member left" style="left:42px;top:100px"><div class="portrait" role="img" aria-label="Portrait photo of team member"></div><h6>NADIA BROOK</h6><div class="role">Head, Mining</div><p>Guides automation in mining sites and heavy operations.</p></div>
  <div class="member right" style="left:238px;top:100px"><div class="portrait" role="img" aria-label="Portrait photo of team member"></div><h6>OWEN HALE</h6><div class="role">Head, Supply</div><p>Designs forecasting and logistics tools for supply chains.</p></div>
  <div class="footer-web"><span class="globe"></span>www.velmoraquill.com</div>
  <div class="footer-copy">© 2025. ALL Rights Reserved.</div>
  <div class="footer-page">Page 07</div>
</section>

<!-- Contact -->
<section class="slide col2 row3">
  <header class="contact-band"><h2>Contact Information</h2><span></span></header>
  <div class="contact-name"><span class="dot"></span><span>Velmora Quill<br>Industries</span></div>
  <div class="contact-row" style="top:106px"><span class="ic"></span><div><small>Call Us</small><span>480.555.0142</span></div></div>
  <div class="contact-row" style="top:126px"><span class="ic"></span><div><small>Address</small><span>4120 Harlow Ave., Suite 210, Tempe,<br>AZ 85281 USA</span></div></div>
  <div class="contact-row" style="top:152px"><span class="ic"></span><div><small>Email</small><span>info@velmoraquill.com</span></div></div>
  <div class="map" role="img" aria-label="Street map showing the office location"></div>
  <div class="footer-web"><span class="globe"></span>www.velmoraquill.com</div>
  <div class="footer-copy">© 2025. ALL Rights Reserved.</div>
  <div class="footer-page">Page 08</div>
</section>

<!-- Brand lockup -->
<div class="brand-panel">
  <div class="name"><span class="dot"></span><span>Velmora Quill<br>Industries</span></div>
  <div class="sub">Engineering AI Transformations</div>
</div>

</body>
</html>
```